Web Site Design and Business Card design for Recruiting Company

There are three major tasks in this project:
1) I need to re-design my newly created website www.talvoro.net using the same logo but creating a totally different recruiting template that will apply better for a recruitment site. I want to use the elements of the Talvoro Network logo (which is the road junction) and red, black and gray colors throughout the website. I need someone to both design and launch the site...
2) I would also like to design a double sided business card using the same logo/colors and elements as described above
3) I would also like to have a small thumbnail logo created. As our large logo cannot be previewed easily on the Pelmwork or on Google Chrome tab images

The design should be contemporary, minimalist and slick

```html
<!DOCTYPE html>
<html lang="en">
<head>
<meta charset="utf-8">
<title>Talvoro Network – Find the Right Job</title>
<link href="https://fonts.googleapis.com/css2?family=Lato:wght@400;700;900&display=swap" rel="stylesheet">
<style>
:root{
  --red:#d8001c;
  --ink:#222222;
  --dark:#151515;
  --grey:#efefef;
  --line:#cfcfcf;
  --muted:#6a6a6a;
  --white:#ffffff;
}
*{box-sizing:border-box;margin:0;padding:0}
html,body{width:1200px;height:4525px;overflow:hidden}
body{font-family:'Lato',sans-serif;color:var(--ink);background:var(--white);position:relative}
.abs{position:absolute}
section,header{position:absolute;left:0;width:1200px}

/* top bar */
.topbar{top:0;height:67px;background:var(--red);color:var(--white)}
.topbar .phone{left:110px;top:20px;display:flex;align-items:center;gap:14px;font-weight:700;font-size:19px}
.social{display:flex;gap:14px;align-items:center}
.social span{width:17px;height:17px;border-radius:50%;background:currentColor;display:block}
.topbar .social{left:690px;top:23px;color:var(--white)}
.topbar .auth{left:870px;top:17px;display:flex;gap:40px;font-weight:700;font-size:18px;align-items:center}
.topbar .auth .login{display:flex;align-items:center;gap:9px}

/* nav */
.navbar{top:67px;height:109px;background:var(--white)}
.brand{left:100px;top:8px;width:140px;height:93px;display:flex;align-items:center;justify-content:center;gap:8px;font-size:17px;font-weight:700;color:var(--ink);border:1px solid #e2e2e2}
.brand i{width:12px;height:12px;background:var(--red);display:block}
.menu{top:50px;display:flex;font-size:19px}
.menu a{position:absolute;white-space:nowrap;color:var(--ink);text-decoration:none}
.menu a.active{color:var(--red)}
.lang{left:917px;top:34px;width:170px;height:54px;background:var(--ink);color:var(--white);font-size:19px;font-weight:700;display:flex;align-items:center;justify-content:space-between;padding:0 18px 0 20px}
.caret{width:0;height:0;border-left:7px solid transparent;border-right:7px solid transparent;border-top:8px solid currentColor}

/* hero */
.hero{top:176px;height:558px}
.hero .photo{inset:0;position:absolute;background:linear-gradient(180deg,#8a8a8a 0%,#a9a9a9 40%,#6b6159 100%)}
.hero h1{position:absolute;top:188px;width:100%;text-align:center;color:var(--white);font-size:47px;font-weight:900;text-shadow:0 2px 6px rgba(0,0,0,.4)}
.search{left:77px;top:280px;width:1047px;height:131px;background:rgba(235,235,235,.93)}
.field{top:35px;height:60px;background:var(--white);border:1px solid #d6d6d6;display:flex;align-items:center;justify-content:space-between;padding:0 22px 0 26px;font-size:17px;color:var(--ink)}
.btn-search{left:817px;top:38px;width:195px;height:58px;background:var(--ink);color:var(--white);font-size:21px;font-weight:700;display:flex;align-items:center;justify-content:center;gap:14px}
.dots{display:flex;gap:10px;justify-content:center;width:100%}
.dots span{width:13px;height:13px;border-radius:50%;background:var(--red)}
.dots span.on{background:var(--white)}

/* welcome */
.welcome{top:734px;height:536px}
.welcome h2{left:112px;top:112px;font-size:47px;font-weight:700;position:absolute}
.red{color:var(--red)}
.welcome p{position:absolute;left:112px;top:198px;width:642px;font-size:14.5px;line-height:31px;color:#333}
.btn-dark{position:absolute;background:var(--ink);color:var(--white);font-size:14px;display:flex;align-items:center;justify-content:center}
.welcome .redblock{left:968px;top:72px;width:232px;height:381px;background:var(--red);border-radius:22px 0 0 22px}
.welcome .person{left:760px;top:96px;width:380px;height:357px;background:linear-gradient(160deg,#d9d9d9,#3b3b3b 70%);border-radius:4px;opacity:.9}

/* services */
.services{top:1270px;height:641px;background:linear-gradient(180deg,#262626,#111)}
.services h2,.cats h2{position:absolute;width:100%;text-align:center;font-size:47px;font-weight:700}
.services h2{top:82px;color:var(--white)}
.svc{position:absolute;top:219px;width:333px;height:250px;border:2px solid var(--white)}
.svc-label{position:absolute;top:510px;width:333px;text-align:center;color:var(--white);font-size:27px;font-weight:700}

/* categories */
.cats{top:1911px;height:794px}
.cats h2{top:110px;color:var(--ink)}
.cats .lead{position:absolute;top:190px;width:100%;text-align:center;font-size:15px;line-height:34px;color:#333}
.cat{position:absolute;width:232px;height:152px;background:var(--grey);border:1px solid var(--line);display:flex;flex-direction:column;align-items:center;justify-content:flex-end;padding-bottom:26px;font-size:14px;color:var(--ink)}
.cat svg{margin-bottom:20px}
.cat.hot{background:var(--red);color:var(--white);outline:2px solid var(--red);outline-offset:-6px;border-color:var(--white)}

/* stats */
.stats{top:2705px;height:483px;background:linear-gradient(160deg,#2c2c2c,#0d0d0d)}
.stat{position:absolute;top:100px;width:220px;text-align:center;color:var(--white)}
.stat .num{font-size:40px}
.stat .bar{width:100px;height:6px;background:var(--red);margin:12px auto 20px}
.stat .lbl{font-size:34px}
.divider{position:absolute;top:110px;width:2px;height:148px;background:#9a9a9a}

/* companies */
.helped{left:124px;top:3039px;width:952px;height:369px;background:var(--white);box-shadow:0 2px 8px rgba(0,0,0,.25)}
.helped h3{position:absolute;top:38px;width:100%;text-align:center;font-size:40px;font-weight:400}
.helped p{position:absolute;top:100px;width:100%;text-align:center;font-size:15px;line-height:28px;color:#333}
.client{position:absolute;top:185px;width:208px;height:94px;border:1px solid #d8d8d8;display:flex;align-items:center;justify-content:center;gap:8px;font-size:17px;font-weight:700;color:#555}
.client i{width:12px;height:12px;border-radius:50%;background:#777;display:block}

/* news */
.news{top:3496px;height:615px}
.news h2{position:absolute;left:112px;top:26px;font-size:47px;font-weight:700}
.card{position:absolute;top:121px;width:318px;height:393px;background:var(--white);box-shadow:0 1px 6px rgba(0,0,0,.2)}
.card .img{height:209px}
.card h4{position:absolute;left:25px;top:232px;font-size:19px;font-weight:400;color:#333}
.card p{position:absolute;left:25px;top:272px;width:268px;font-size:11px;line-height:22px;color:#555}
.card .meta{position:absolute;left:25px;right:25px;top:358px;display:flex;justify-content:space-between;font-size:11px;color:#555}
.card .meta span{display:flex;align-items:center;gap:8px}

/* footer */
.footer{top:4111px;height:414px;background:var(--dark);color:var(--white)}
.contact{position:absolute;top:63px;width:260px;text-align:center;font-size:16px;line-height:28px}
.contact .ic{width:66px;height:66px;border-radius:50%;background:var(--red);margin:0 auto 20px;display:flex;align-items:center;justify-content:center}
.fnav a{position:absolute;top:228px;color:var(--white);text-decoration:none;font-size:19px}
.footer .social{left:528px;top:296px;color:var(--white);gap:23px}
.footer hr{position:absolute;left:72px;top:350px;width:978px;border:0;border-top:1px solid #555}
.copy{position:absolute;left:72px;top:367px;font-size:12.5px}
</style>
</head>
<body>

<header class="topbar">
  <div class="abs phone">
    <svg width="30" height="30" viewBox="0 0 24 24" fill="#fff"><path d="M6.6 10.8a15 15 0 0 0 6.6 6.6l2.2-2.2a1 1 0 0 1 1-.25 11.4 11.4 0 0 0 3.6.57 1 1 0 0 1 1 1V20a1 1 0 0 1-1 1A17 17 0 0 1 3 4a1 1 0 0 1 1-1h3.5a1 1 0 0 1 1 1c0 1.25.2 2.45.57 3.57a1 1 0 0 1-.25 1z"/></svg>
    +1-555-014-0636
  </div>
  <div class="abs social" aria-label="Social links"><span></span><span></span><span></span><span></span></div>
  <div class="abs auth">
    <div class="login">
      <svg width="24" height="22" viewBox="0 0 24 22" fill="none" stroke="#fff" stroke-width="2"><path d="M9 3h11v16H9"/><path d="M2 11h11M9 7l4 4-4 4"/></svg>
      Login
    </div>
    <div>Register</div>
  </div>
</header>

<header class="navbar">
  <div class="abs brand"><i></i>Talvoro Network</div>
  <nav class="abs menu" style="left:0;top:50px">
    <a class="active" style="left:265px">Home</a>
    <a style="left:380px">Jobs</a>
    <a style="left:487px">Companies</a>
    <a style="left:648px">About us</a>
    <a style="left:787px">Contact Us</a>
  </nav>
  <div class="abs lang">Language <span class="caret"></span></div>
</header>

<section class="hero">
  <div class="photo" role="img" aria-label="Overhead photo of a team working around an office desk"></div>
  <h1>FIND THE RIGHT JOB</h1>
  <div class="abs search">
    <div class="abs field" style="left:18px;width:262px">All Categories <span class="caret"></span></div>
    <div class="abs field" style="left:297px;width:236px">Location <span class="caret"></span></div>
    <div class="abs field" style="left:550px;width:236px">Keyword <span class="caret"></span></div>
    <div class="abs btn-search">
      <svg width="28" height="28" viewBox="0 0 24 24" fill="none" stroke="#fff" stroke-width="2.4"><circle cx="10" cy="10" r="7"/><path d="M15 15l6 6"/></svg>
      Search
    </div>
  </div>
  <div class="abs dots" style="top:523px"><span class="on"></span><span></span><span></span></div>
</section>

<section class="welcome">
  <h2>Welcome To <span class="red">Talvoro</span></h2>
  <p>Lorem ipsum dolor sit amet, consectetur adipiscing elit, sed do eiusmod tempor incididunt ut labore et dolore magna aliqua. Quis ipsum suspendisse ultrices gravida. Risus commodo viverra maecenas accumsan lacus vel facilisis. Lorem ipsum dolor sit amet, consectetur adipiscing elit, sed do eiusmod tempor incididunt ut labore et dolore magna aliqua. Quis ipsum suspendisse ultrices gravida. Risus commodo viverra maecenas accumsan lacus vel facilisis.</p>
  <div class="btn-dark" style="left:111px;top:397px;width:120px;height:36px">Read More</div>
  <div class="abs redblock"></div>
  <div class="abs person" role="img" aria-label="Photo of a smiling businessman in a suit pointing toward the text"></div>
</section>

<section class="services">
  <h2>Our Service</h2>
  <div class="svc" style="left:67px;background:linear-gradient(135deg,#0d2a4a,#3a8fd0 60%,#0b1d33)" role="img" aria-label="Photo of digital devices floating over an open hand"></div>
  <div class="svc" style="left:434px;background:linear-gradient(180deg,#0a1a2e,#1d3a5c 55%,#0b1420)" role="img" aria-label="Photo of a city skyline at night with network light arcs"></div>
  <div class="svc" style="left:800px;background:linear-gradient(135deg,#e8eef6,#9fb8d6 55%,#5a6f8a)" role="img" aria-label="Photo of a hand with a pen over financial charts"></div>
  <div class="svc-label" style="left:67px">Information Technology</div>
  <div class="svc-label" style="left:434px">Telecommunications</div>
  <div class="svc-label" style="left:800px">Accounting &amp; Finance</div>
</section>

<section class="cats">
  <h2>Popular <span class="red">Categories</span></h2>
  <div class="lead">One of our jobs has some kind of flexibility option - such as telecommutinga part-time<br>schedule or a flexible or flextime schedule.</div>

  <div class="cat" style="left:100px;top:308px">
    <svg width="64" height="64" viewBox="0 0 64 64" fill="none" stroke="var(--red)" stroke-width="2.5"><path d="M10 54L44 14M44 14c4-6 12-8 10 2s-10 12-14 8"/><path d="M54 54L20 20M12 8l14 14M8 12l14 14M16 6l-10 10"/></svg>
    Restaurant / Food Service</div>
  <div class="cat" style="left:357px;top:308px">
    <svg width="64" height="64" viewBox="0 0 64 64" fill="none" stroke="var(--red)" stroke-width="2.5"><rect x="12" y="18" width="40" height="40"/><path d="M28 6h8v6h6v8h-6v6h-8v-6h-6v-8h6z"/><path d="M18 30h6v6h-6zM40 30h6v6h-6zM18 44h6v6h-6zM40 44h6v6h-6zM28 44h8v14h-8z"/></svg>
    Healthcare</div>
  <div class="cat" style="left:612px;top:308px">
    <svg width="64" height="64" viewBox="0 0 64 64" fill="none" stroke="var(--red)" stroke-width="2.5"><circle cx="32" cy="22" r="10"/><circle cx="18" cy="14" r="6"/><circle cx="46" cy="14" r="6"/><path d="M8 40l14-4 14 8 16-6-10 16H20z"/><path d="M29 18v8h6"/></svg>
    Accounting / Finance</div>
  <div class="cat" style="left:862px;top:308px">
    <svg width="64" height="64" viewBox="0 0 64 64" fill="none" stroke="var(--red)" stroke-width="2.5"><circle cx="32" cy="20" r="4"/><path d="M24 12a12 12 0 0 0 0 16M40 12a12 12 0 0 1 0 16M18 6a20 20 0 0 0 0 28M46 6a20 20 0 0 1 0 28M32 24L20 56h24zM14 56h36"/></svg>
    Telecommunications</div>

  <div class="cat" style="left:100px;top:492px">
    <svg width="64" height="64" viewBox="0 0 64 64" fill="none" stroke="var(--red)" stroke-width="2.5"><circle cx="32" cy="30" r="18"/><circle cx="32" cy="30" r="8"/><path d="M32 6v6M32 48v6M8 30h6M50 30h6M15 13l4 4M45 43l4 4M15 47l4-4M45 17l4-4"/></svg>
    Information Technology</div>
  <div class="cat" style="left:357px;top:492px">
    <svg width="64" height="64" viewBox="0 0 64 64" fill="none" stroke="var(--red)" stroke-width="2.5"><rect x="6" y="8" width="52" height="38"/><path d="M6 16h52M14 26h16M14 32h24M14 38h12M24 46l-4 10h24l-4-10"/></svg>
    Designer</div>
  <div class="cat" style="left:612px;top:492px">
    <svg width="64" height="64" viewBox="0 0 64 64" fill="none" stroke="var(--red)" stroke-width="2.5"><rect x="6" y="20" width="52" height="30"/><path d="M22 50l-4 8h28l-4-8M24 8l8-4 8 4v10l-8 4-8-4zM24 8l8 4 8-4M32 12v10"/></svg>
    Developer</div>
  <div class="cat hot" style="left:862px;top:492px">
    <svg width="64" height="64" viewBox="0 0 64 64" fill="none" stroke="#fff" stroke-width="2.5"><circle cx="32" cy="14" r="6"/><circle cx="14" cy="18" r="5"/><circle cx="50" cy="18" r="5"/><path d="M20 36c0-8 5-12 12-12s12 4 12 12zM4 38c0-7 4-10 10-10M60 38c0-7-4-10-10-10M8 44h48M32 44v14M22 58h20"/></svg>
    Human Resource</div>
</section>

<section class="stats">
  <div class="stat" style="left:70px"><div class="num">3000</div><div class="bar"></div><div class="lbl">Companies</div></div>
  <div class="divider" style="left:318px"></div>
  <div class="stat" style="left:346px"><div class="num">1257</div><div class="bar"></div><div class="lbl">Live Jobs</div></div>
  <div class="divider" style="left:609px"></div>
  <div class="stat" style="left:623px"><div class="num">700</div><div class="bar"></div><div class="lbl">Resume</div></div>
  <div class="divider" style="left:875px"></div>
  <div class="stat" style="left:903px"><div class="num">3782</div><div class="bar"></div><div class="lbl">Resources</div></div>
</section>

<div class="abs helped">
  <h3>Companies We've Helped</h3>
  <p>Lorem ipsum dolor sit amet, consectetur adipiscing elit, sed do eiusmod tempor<br>incididunt ut labore et dolore magna aliqua. Quis ipsum suspendisse ultrices gravida.</p>
  <div class="client" style="left:14px"><i></i>Norvale</div>
  <div class="client" style="left:247px"><i></i>Quintex</div>
  <div class="client" style="left:481px"><i></i>Brightmoor</div>
  <div class="client" style="left:716px"><i></i>Lakespire</div>
  <div class="abs dots" style="top:325px"><span></span><span></span><span></span></div>
</div>

<section class="news">
  <h2>Latest <span class="red">News</span></h2>
  <article class="card" style="left:97px">
    <div class="img" role="img" aria-label="Photo of a person writing with a pen beside a calculator" style="background:linear-gradient(135deg,#f3d2a8,#c48a52 60%,#7a5432)"></div>
    <h4>Darien Clients</h4>
    <p>Lorem ipsum dolor sit amet, consectetur adipiscing elit, sed do eiusmod tempor incididunt ut labore et dolore magna aliqua. Ut enim ad minim veniam,</p>
    <div class="meta"><span>&#9719; Sep 10' 19</span><span>&#9993; 5 Coments</span></div>
  </article>
  <article class="card" style="left:440px">
    <div class="img" role="img" aria-label="Photo of two professionals shaking hands in an office" style="background:linear-gradient(135deg,#6b7a80,#c9ced0 55%,#3c4448)"></div>
    <h4>Lorem Ipsum is simply</h4>
    <p>Lorem ipsum dolor sit amet, consectetur adipiscing elit, sed do eiusmod tempor incididunt ut labore et dolore magna aliqua. Ut enim ad minim veniam,</p>
    <div class="meta"><span>&#9719; Sep 10' 19</span><span>&#9993; 5 Coments</span></div>
  </article>
  <article class="card" style="left:782px">
    <div class="img" role="img" aria-label="Photo of two businessmen talking at a meeting table" style="background:linear-gradient(135deg,#d9d6cf,#6a5e52 55%,#222)"></div>
    <h4>Greenwich Clients</h4>
    <p>Lorem ipsum dolor sit amet, consectetur adipiscing elit, sed do eiusmod tempor incididunt ut labore et dolore magna aliqua. Ut enim ad minim veniam,</p>
    <div class="meta"><span>&#9719; Sep 10' 19</span><span>&#9993; 5 Coments</span></div>
  </article>
  <div class="abs dots" style="top:570px"><span></span><span></span><span></span></div>
</section>

<footer class="footer" style="position:absolute;left:0;width:1200px">
  <div class="contact" style="left:223px">
    <div class="ic"><svg width="24" height="24" viewBox="0 0 24 24" fill="#fff"><path d="M6.6 10.8a15 15 0 0 0 6.6 6.6l2.2-2.2a1 1 0 0 1 1-.25 11.4 11.4 0 0 0 3.6.57 1 1 0 0 1 1 1V20a1 1 0 0 1-1 1A17 17 0 0 1 3 4a1 1 0 0 1 1-1h3.5a1 1 0 0 1 1 1c0 1.25.2 2.45.57 3.57a1 1 0 0 1-.25 1z"/></svg></div>
    +1-555-014-0636</div>
  <div class="contact" style="left:469px">
    <div class="ic"><svg width="22" height="28" viewBox="0 0 22 28" fill="#fff"><path d="M11 0a10 10 0 0 0-10 10c0 8 10 18 10 18s10-10 10-18A10 10 0 0 0 11 0zm0 14a4 4 0 1 1 0-8 4 4 0 0 1 0 8z"/></svg></div>
    4821 Harlow Ave Ste 210;<br>Fairview, ST 00000</div>
  <div class="contact" style="left:708px">
    <div class="ic"><svg width="26" height="20" viewBox="0 0 26 20" fill="#fff"><path d="M0 2h26v16H0z"/><path d="M0 2l13 9 13-9" stroke="#d8001c" stroke-width="2" fill="none"/></svg></div>
    info@talvoro.net</div>
  <nav class="fnav">
    <a style="left:290px">Home</a>
    <a style="left:404px">Jobs</a>
    <a style="left:510px">Companies</a>
    <a style="left:671px">About us</a>
    <a style="left:811px">Contact Us</a>
  </nav>
  <div class="abs social" aria-label="Social links"><span></span><span></span><span></span><span></span></div>
  <hr>
  <div class="copy">© 2019 Copyrights Company Name | All Rights Reserved</div>
</footer>

</body>
</html>
```